Varnex Consulting Business card design.

See our website www.varnexconsulting.example which will give you a good idea of what we are about. The font is called 'Play'.

I'd like a standout business card in keeping with the themes and branding on the website

Target Market(s)

professionals. HR directors

Industry/Entity Type

Business

Contact Information for Business Card

Varnex Consulting PO Box 3172 Merrowdale NSW 2291 1300 485 193 Gavin Threlkeld Principal email: career@varnexconsulting.example ABN: 71203948865

Font styles to use
Other font styles liked:
• Play

Requirements
Must have
• Must have same design colours and branding as website.
• On back I'd prefer a list of the things we do which appears below the name at the header on the website

```html
<!DOCTYPE html>
<html lang="en">
<head>
<meta charset="utf-8">
<title>Varnex Consulting – Business Card</title>
<link rel="stylesheet" href="https://fonts.googleapis.com/css2?family=Play:wght@400;700&family=Arimo:wght@400;700&display=swap">
<style>
  :root {
    --canvas-bg: #e9e9e9;
    --card-white: #ffffff;
    --card-grey: #d2d2d2;
    --brand-blue: #1d8fdb;
    --brand-navy: #0e2539;
    --ink-dark: #1a2a38;
    --ink-grey: #555b61;
    --text-light: #ffffff;
    --label-blue: #2a9ae6;
  }
  * { box-sizing: border-box; margin: 0; padding: 0; }
  html, body { width: 1200px; height: 950px; overflow: hidden; }
  body {
    background: var(--canvas-bg);
    display: flex;
    flex-direction: column;
    align-items: center;
    justify-content: center;
    gap: 50px;
    font-family: "Arimo", Arial, sans-serif;
  }
  .card {
    width: 700px;
    height: 400px;
    position: relative;
    overflow: hidden;
    box-shadow: 0 6px 18px rgba(0,0,0,0.18);
  }
  .wordmark {
    font-family: "Play", sans-serif;
    font-weight: 400;
    letter-spacing: 3px;
    color: var(--ink-dark);
    text-transform: uppercase;
    white-space: nowrap;
  }

  /* Back */
  .card-back {
    background: linear-gradient(160deg, var(--card-white) 0%, #f1f1f1 45%, var(--card-grey) 100%);
  }
  .card-back .wordmark {
    position: absolute;
    left: 0; right: 0;
    top: 150px;
    text-align: center;
    font-size: 40px;
  }
  .card-back .services {
    position: absolute;
    right: 70px;
    top: 222px;
    font-size: 17px;
    color: var(--ink-grey);
    letter-spacing: 0.5px;
  }

  /* Front */
  .card-front { background: var(--card-white); }
  .card-front .logo-area {
    height: 148px;
    display: flex;
    align-items: center;
    justify-content: center;
  }
  .card-front .wordmark { font-size: 40px; }
  .name-band {
    height: 86px;
    background: var(--brand-blue);
    color: var(--text-light);
    text-align: center;
    padding-top: 14px;
    border-bottom: 2px solid var(--text-light);
  }
  .name-band .person { font-size: 25px; font-weight: 700; letter-spacing: 0.5px; }
  .name-band .role { font-size: 17px; margin-top: 3px; }
  .contact-band {
    height: 166px;
    background: var(--brand-navy);
    color: var(--text-light);
    text-align: center;
    padding-top: 24px;
    font-size: 18px;
    line-height: 1.55;
  }
  .contact-band .label { color: var(--label-blue); }
</style>
</head>
<body>
  <section class="card card-back" aria-label="Card back">
    <p class="wordmark">Varnex Consulting</p>
    <p class="services">Career Coaching | Leadership | Outplacement</p>
  </section>

  <section class="card card-front" aria-label="Card front">
    <div class="logo-area">
      <p class="wordmark">Varnex Consulting</p>
    </div>
    <div class="name-band">
      <p class="person">Gavin Threlkeld</p>
      <p class="role">Principal</p>
    </div>
    <div class="contact-band">
      <p class="address">PO Box 3172 Merrowdale NSW 2291</p>
      <p><span class="label">Phone:</span> 1300 485 193 &nbsp;<span class="label">Email:</span> career@varnexconsulting.example</p>
      <p><span class="label">Web:</span> www.varnexconsulting.example</p>
    </div>
  </section>
</body>
</html>
```